Harbor Wonder Hour - A magic website for a monthly modern magic show

Looking to build a website to promote my new monthly magic show

Sites like this. https://velvetloftshow.example/ https://sevencuriouscardsnight.example/

Target Market(s)

18-65 year old men and women who enjoy live entertainment especially magic

Industry/Entity Type

Entertainment

Coding

Coded - Design and coding required

Number of Pages Required

3 page

Colors

Designer to choose colors to be used in the design.

Requirements
Must have
• Wanting a wordpress site.
• Contact form, media section for photos and videos to be posted.
• A “reviews/testimonials” section.

```html
<!DOCTYPE html>
<html lang="en">
<head>
<meta charset="utf-8">
<title>Dean Hollister Magic</title>
<link href="https://fonts.googleapis.com/css2?family=Titillium+Web:wght@400;600;700;900&family=Poppins:wght@400;500&display=swap" rel="stylesheet">
<style>
:root{
  --gold:#c48f3e;
  --gold-bright:#f3b23f;
  --gold-deep:#a9772c;
  --band:#d5a43a;
  --ink:#161514;
  --ink-2:#1f1d1b;
  --paper:#f8e4a4;
  --white:#ffffff;
  --muted:#d9d4cc;
}
*{box-sizing:border-box;margin:0;padding:0}
html,body{width:1200px;height:4800px;overflow:hidden}
body{position:relative;background:var(--ink);font-family:"Poppins",sans-serif;color:var(--white)}
.abs{position:absolute}
.heading{font-family:"Titillium Web",sans-serif;font-weight:700;text-transform:uppercase;text-align:center;left:0;width:1200px}
.btn{position:absolute;display:flex;align-items:center;justify-content:center;font-family:"Titillium Web",sans-serif;font-weight:700;font-size:17px;text-transform:uppercase;color:var(--white);background:var(--gold);transform:skewX(-12deg);border-right:4px solid var(--white);border-left:4px solid var(--white)}
.btn span{transform:skewX(12deg)}
.btn.dark{background:var(--ink)}
.btn.light{background:var(--white);color:var(--ink);border-color:var(--ink)}

/* hero */
.hero-photo{left:0;top:0;width:1200px;height:840px;background:radial-gradient(circle at 1050px 190px,#e8dfcf 0,#7d6e58 80px,#2b241d 210px,#14110e 480px),linear-gradient(90deg,#1d1813,#0f0d0b)}
.hero-figure{left:90px;top:140px;width:420px;height:580px;border-radius:200px 200px 40px 40px;background:linear-gradient(160deg,#3a3129,#1a1612 70%)}
.brand{left:140px;top:46px;display:flex;align-items:center;gap:12px;font-family:"Titillium Web",sans-serif;font-weight:700;font-size:17px;color:var(--gold);text-transform:uppercase;line-height:1.1}
.brand i{width:26px;height:26px;border:2px solid var(--gold);border-radius:50%}
.phone{left:676px;top:40px;width:172px;height:38px;font-size:18px}
.nav{right:146px;top:108px;display:flex;gap:22px;font-family:"Titillium Web",sans-serif;font-weight:700;font-size:15px;text-transform:uppercase}
.nav a{color:var(--white);text-decoration:none;position:relative}
.nav a.on:after{content:"";position:absolute;left:0;right:0;bottom:-12px;height:3px;background:var(--gold)}
.kicker{right:145px;top:386px;font-family:"Titillium Web",sans-serif;font-weight:600;font-size:18px;text-transform:uppercase}
.title{right:145px;top:418px;font-family:"Titillium Web",sans-serif;font-weight:900;font-size:46px;text-transform:uppercase;letter-spacing:-.5px}
.scroll{left:564px;top:611px;width:120px;height:120px;border:2px solid var(--muted);border-radius:50%;text-align:center;font-size:11px;padding-top:40px;text-transform:uppercase}

/* promo band */
.promo-text{top:828px;font-size:28px;line-height:43px;color:var(--white)}
.rule{left:573px;top:976px;width:54px;height:3px;background:var(--white)}

/* services */
.section-mark{width:34px;height:34px;border:3px solid var(--gold);border-radius:50%;left:583px}
.intro{top:1350px;left:0;width:1200px;text-align:center;font-size:13px;line-height:24px}
.service-photo{left:790px;top:1210px;width:410px;height:790px;background:linear-gradient(180deg,#2a2420,#15120f);border-radius:180px 0 0 0}
.disc{border-radius:50%;display:flex;flex-direction:column;align-items:center;text-align:center;overflow:hidden}
.disc.gold{background:var(--gold-bright);width:286px;height:286px;padding:74px 40px 0}
.disc h3{font-family:"Titillium Web",sans-serif;font-weight:600;font-size:19px;text-transform:uppercase;margin:14px 0 8px}
.disc p{font-size:12.5px;line-height:24px;color:#fff7e2}
.disc .icon{width:52px;height:60px;border:3px solid var(--white);border-radius:6px}
.disc.main{width:374px;height:374px;background:var(--ink-2);border:8px solid var(--white);box-shadow:0 0 0 8px var(--gold-bright);padding:46px 44px 0}
.disc.main p{font-size:13.5px;line-height:26px;color:var(--white)}
.disc.main .more{font-weight:500;font-size:12px;text-decoration:underline;margin-top:8px}

/* video */
.video{left:143px;top:2120px;width:912px;height:462px;background:linear-gradient(90deg,#c9c3b8,#5b5651 45%,#2d2a27 70%,#9c968c)}
.play{left:540px;top:2302px;width:120px;height:120px;border:4px solid var(--gold);border-radius:50%}
.fit-title{top:2628px;font-size:36px;text-transform:none;color:var(--white)}
.fit{top:2729px;width:215px;height:202px;background:var(--gold);text-align:center;padding-top:32px;font-family:"Titillium Web",sans-serif;font-weight:600;font-size:15px;line-height:20px}
.fit .ring{width:92px;height:92px;border-radius:50%;background:var(--white);margin:0 auto 18px;display:flex;align-items:center;justify-content:center}

/* media */
.media-title{top:3186px;font-size:38px}
.card{top:3279px;width:293px;height:341px;background:var(--white);color:#555;border-radius:4px;overflow:hidden}
.card .shot{height:182px;background:linear-gradient(135deg,#5a4a3c,#1e1915)}
.card .meta{display:flex;align-items:center;gap:10px;padding:14px 16px 8px;font-size:10.5px;line-height:13px;color:#333}
.card .meta i{width:26px;height:26px;border-radius:50%;background:#3b5ea8;flex:none}
.card .meta b{font-weight:400;margin-left:auto}
.card p{padding:0 18px;font-size:12px;line-height:19px}
.card .stats{padding:10px 18px;font-size:10px;color:#333}
.arrow{top:3420px;width:30px;height:56px}

/* testimonial */
.paper-back{left:140px;top:3720px;width:900px;height:390px;background:#f6d68c;transform:rotate(-3deg)}
.paper{left:149px;top:3754px;width:904px;height:345px;background:var(--paper);border:6px solid var(--gold-deep);text-align:center;color:#3d3426}
.paper h2{font-family:"Titillium Web",sans-serif;font-weight:700;font-size:34px;margin-top:40px;color:#2b2419}
.stars{font-size:22px;color:var(--gold);letter-spacing:2px;margin:4px 0 14px}
.quote{font-size:13.5px;line-height:30px;padding:0 60px}
.who{margin-top:12px;font-size:15px}

/* contact */
.contact-title{top:4232px;font-size:38px}
.partner{background:var(--white);color:#6b6b6b;display:flex;align-items:center;justify-content:center;font-family:"Titillium Web",sans-serif;font-weight:600;font-size:20px}
.field{background:transparent;border:1px solid #b8b2a8;font-size:12px;color:var(--white);padding:10px 12px}
.submit{left:443px;top:4564px;width:177px;height:40px;background:var(--gold);font-family:"Titillium Web",sans-serif;font-weight:700;font-size:17px;display:flex;align-items:center;justify-content:center}

.footer{left:0;top:4676px;width:1200px;height:124px;background:#0d0c0b}
.footer p{position:absolute;left:143px;top:58px;font-size:16px}
.social{top:4725px;width:40px;height:40px;border:2px solid var(--white);border-radius:50%}
</style>
</head>
<body>

<!-- hero -->
<div class="abs hero-photo" role="img" aria-label="Dimly lit stage with a spotlight and a magician in a suit tossing playing cards between his hands"></div>
<div class="abs hero-figure" role="img" aria-label="Magician in a dark suit throwing playing cards"></div>

<div class="abs brand"><i></i><span>Dean Hollister<br>Magic</span></div>
<div class="btn light phone"><span>555-014-2270</span></div>
<div class="btn" style="left:872px;top:40px;width:182px;height:38px"><span>Book Tickets</span></div>
<nav class="abs nav">
  <a class="on">Home</a><a>Corporate Events</a><a>Private Events</a><a>About</a><a>Reviews</a><a>Contact Us</a>
</nav>
<div class="abs kicker">More than entertainment – an experience</div>
<div class="abs title">Award Winning Magic</div>
<div class="btn" style="left:639px;top:494px;width:194px;height:46px"><span>Book Tickets</span></div>
<div class="btn" style="left:853px;top:494px;width:200px;height:46px"><span>Watch Trailer</span></div>
<div class="abs scroll">Scroll down
  <svg width="20" height="44" viewBox="0 0 20 44" style="display:block;margin:6px auto 0"><path d="M10 0V40M3 32L10 41L17 32" stroke="#d9d4cc" stroke-width="1.5" fill="none"/></svg>
</div>

<!-- promo band -->
<svg class="abs" style="left:0;top:690px" width="1200" height="520" viewBox="0 0 1200 520">
  <polygon points="0,10 1200,140 1200,390 0,510" fill="#d5a43a"/>
</svg>
<div class="abs heading promo-text">Get your tickets to my live show “Mind Drift”<br>in Roseville, CA on April 26th. An evening of magic<br>and mysteries of the mind.</div>
<div class="abs rule"></div>
<div class="btn dark" style="left:499px;top:1015px;width:200px;height:47px"><span>Book Tickets</span></div>

<!-- services -->
<div class="abs service-photo" role="img" aria-label="Magician in a suit fanning a deck of cards"></div>
<div class="abs section-mark" style="top:1236px"></div>
<div class="abs heading" style="top:1286px;font-size:38px">Our Services</div>
<p class="intro">From weddings to corporate events to your weekly happy hour, Dean Hollister is a professional magician that<br>provides a world class close-up magic act for the Seattle metro area.</p>

<div class="abs disc gold" style="left:142px;top:1497px">
  <div class="icon"></div>
  <h3>Private Events</h3>
  <p>Need a fresh idea for a valued holiday, birthday party, fundraiser, or any variety of private event? Turn your event into an</p>
</div>
<div class="abs disc gold" style="left:770px;top:1497px">
  <div class="icon" style="border-radius:50%;width:56px;height:56px"></div>
  <h3>Wedding Entertainment</h3>
  <p>Looking for unique entertainment for your wedding reception, bachelor or bachelorette party, or rehearsal dinner? Make your</p>
</div>
<div class="abs disc main" style="left:405px;top:1445px">
  <div class="icon" style="width:70px;height:72px"></div>
  <h3>Corporate Functions</h3>
  <p>What if you could change “just another day at the office” into an unforgettable experience that will get your company event started off on the right foot? Dean provides a crisp corporate magic</p>
  <div class="more">READ MORE &gt;</div>
</div>

<!-- video -->
<div class="abs video" role="img" aria-label="Video still of the magician holding a fanned deck of cards in front of a brick wall"></div>
<div class="abs play"><svg width="112" height="112" viewBox="0 0 112 112"><polygon points="44,34 80,56 44,78" fill="none" stroke="#c48f3e" stroke-width="4"/></svg></div>

<div class="abs heading fit-title">How Does Magic Fit into My Event?</div>
<div class="abs fit" style="left:143px"><div class="ring"><svg width="50" height="50" viewBox="0 0 50 50" fill="none" stroke="#c48f3e" stroke-width="2.5"><circle cx="17" cy="16" r="7"/><circle cx="34" cy="16" r="7"/><path d="M5 44c0-9 5-15 12-15s12 6 12 15M23 44c0-9 4-15 11-15s11 6 11 15"/></svg></div>High Quality and<br>Family Friendly</div>
<div class="abs fit" style="left:376px"><div class="ring"><svg width="50" height="50" viewBox="0 0 50 50" fill="none" stroke="#c48f3e" stroke-width="2.5"><rect x="14" y="6" width="22" height="34" rx="3"/><path d="M21 34h8"/></svg></div>Flexible<br>to Your Needs</div>
<div class="abs fit" style="left:607px"><div class="ring"><svg width="50" height="50" viewBox="0 0 50 50" fill="none" stroke="#c48f3e" stroke-width="2.5"><rect x="6" y="10" width="34" height="30" rx="2"/><path d="M6 18h34M14 6v8M32 6v8"/><circle cx="36" cy="36" r="8" fill="#fff"/><path d="M36 32v4l3 2"/></svg></div>Covers up wait<br>times</div>
<div class="abs fit" style="left:840px"><div class="ring"><svg width="50" height="50" viewBox="0 0 50 50" fill="none" stroke="#c48f3e" stroke-width="2.5"><path d="M10 40L25 8L40 40Z"/><circle cx="25" cy="28" r="4"/></svg></div>Interactive<br>Entertainment</div>
<svg class="abs" style="left:352px;top:2820px" width="500" height="20" viewBox="0 0 500 20"><g fill="#c48f3e"><polygon points="6,2 14,10 6,18"/><polygon points="238,2 246,10 238,18"/><polygon points="471,2 479,10 471,18"/></g></svg>

<!-- media & testimonial band -->
<svg class="abs" style="left:0;top:3040px" width="1200" height="1180" viewBox="0 0 1200 1180">
  <polygon points="0,0 1200,95 1200,1140 0,1100" fill="#c48f3e"/>
</svg>
<div class="abs section-mark" style="top:3130px;border-color:#fff"></div>
<div class="abs heading media-title">Our Media</div>

<svg class="abs arrow" style="left:76px" viewBox="0 0 30 56"><path d="M26 2L4 28L26 54" fill="none" stroke="#3a2c18" stroke-width="2"/></svg>
<svg class="abs arrow" style="left:1094px" viewBox="0 0 30 56"><path d="M4 2L26 28L4 54" fill="none" stroke="#3a2c18" stroke-width="2"/></svg>

<div class="abs card" style="left:130px">
  <div class="shot" role="img" aria-label="Magician holding a card in front of a brick wall"></div>
  <div class="meta"><i></i><span>Dean Hollister<br>@DeanHollister</span><b>Apr 29th, 2019</b></div>
  <p>Lorem ipsum dolor sit amet, consectetur adipiscing elit, sed do eiusmod tempor incididunt ut labore et dolore</p>
  <div class="stats">312 ★ &nbsp;343 ⟳ &nbsp;↩</div>
</div>
<div class="abs card" style="left:453px">
  <div class="shot" role="img" aria-label="Video still of playing cards flying between the magician's hands"></div>
  <div class="meta"><i style="background:#3aa0e0"></i><span>Dean Hollister<br>@DeanHollister</span><b>Apr 29th, 2019</b></div>
  <p>Lorem ipsum dolor sit amet, consectetur adipiscing elit, sed do eiusmod tempor incididunt ut labore et dolore</p>
  <div class="stats">312 ★ &nbsp;343 ⟳ &nbsp;↩</div>
</div>
<div class="abs card" style="left:773px">
  <div class="shot" role="img" aria-label="Magician performing for guests at a dinner table"></div>
  <div class="meta"><i></i><span>Dean Hollister<br>@DeanHollister</span><b>Apr 29th, 2019</b></div>
  <p>Lorem ipsum dolor sit amet, consectetur adipiscing elit, sed do eiusmod tempor incididunt ut labore et dolore</p>
  <div class="stats">312 ★ &nbsp;343 ⟳ &nbsp;↩</div>
</div>

<div class="abs paper-back"></div>
<div class="abs paper">
  <h2>TESTIMONIALS</h2>
  <div class="stars">“ ☆☆☆☆☆ ”</div>
  <p class="quote">“We've had the privilege of having Dean perform at our company Holiday party for the past two years. He is nothing short of amazing! Our staff looks forward to Dean's jaw dropping, astounding magic tricks every year. He is so talented at what he does, not to mention professional, interactive and so personable. Dean is so great to work with and liked by all!! We are looking forward to having him back for years to come.”</p>
  <p class="who">Claire Dunmore ~ Rennhaus Motors</p>
  <svg class="abs" style="left:22px;top:150px" width="20" height="36" viewBox="0 0 20 36"><path d="M18 2L3 18L18 34" fill="none" stroke="#8a6a35" stroke-width="2"/></svg>
  <svg class="abs" style="right:22px;top:150px" width="20" height="36" viewBox="0 0 20 36"><path d="M2 2L17 18L2 34" fill="none" stroke="#8a6a35" stroke-width="2"/></svg>
</div>

<!-- contact -->
<div class="abs section-mark" style="top:4176px"></div>
<div class="abs heading contact-title">Contact Us</div>
<div class="abs partner" style="left:143px;top:4326px;width:261px;height:80px">Northway Systems</div>
<div class="abs partner" style="left:143px;top:4415px;width:129px;height:79px;font-size:15px">Rennhaus</div>
<div class="abs partner" style="left:283px;top:4415px;width:121px;height:79px;font-size:15px">Vantor Auto</div>
<div class="abs partner" style="left:143px;top:4505px;width:261px;height:78px">Pulse Gym</div>

<div class="abs field" style="left:443px;top:4327px;width:297px;height:38px">First Name</div>
<div class="abs field" style="left:756px;top:4327px;width:300px;height:38px">Mobile Number</div>
<div class="abs field" style="left:443px;top:4383px;width:297px;height:38px">Last Name</div>
<div class="abs field" style="left:756px;top:4383px;width:300px;height:38px">Email</div>
<div class="abs field" style="left:443px;top:4443px;width:613px;height:97px">Message</div>
<div class="abs submit">SUBMIT</div>

<footer class="abs footer"><p>Dean Hollister © 2019 All Rights Reserved | Privacy Policy</p></footer>
<div class="abs social" style="left:921px" aria-label="Social profile"></div>
<div class="abs social" style="left:969px" aria-label="Social profile"></div>
<div class="abs social" style="left:1018px" aria-label="Video channel"></div>

</body>
</html>
```